Silver Bloom Marisol's Cleaning Service Business Cards Project

A business card with all contact details with logo design on there (already have a logo) eye catching Logo and contact info on one side, full logo on the back, must target upper class residential and corporate companies, fitness companies, still keep it on the feminine side of things , must look elegant

Target Market(s)

Upper class homes and corporate companies

Industry/Entity Type

Cleaning Service

Contact Information for Business Card

Name: Marisol Quenby
Position: Director
ABN: 31647209853
Email: marisolssilvercleaning@tidymail.example
Number: 0417906354

Font styles to use
Decorative

Colors

Designer to choose colors to be used in the design.

Requirements
Must have
• Available Sydney Wide, contact info and logo on one side, full logo on the back
Nice to have
• Professional appearance
Should not have
• Cheap advert looking stuff

```html
<!DOCTYPE html>
<html lang="en">
<head>
<meta charset="utf-8">
<title>Silver Bloom Marisol's Cleaning Service – Business Cards</title>
<link rel="stylesheet" href="https://fonts.googleapis.com/css2?family=Noto+Serif:wght@700&family=Roboto:wght@400;500&display=swap">
<style>
  :root {
    --backdrop: #2f2f2f;
    --card: #232323;
    --teal: #6dcfd0;
    --white: #f3f3f3;
  }
  * { box-sizing: border-box; margin: 0; padding: 0; }
  html, body {
    width: 1200px;
    height: 900px;
    overflow: hidden;
    background: var(--backdrop);
  }
  .sheet {
    width: 1200px;
    height: 900px;
    display: flex;
    flex-direction: column;
    align-items: center;
    justify-content: center;
    gap: 40px;
  }
  .card {
    position: relative;
    width: 700px;
    height: 400px;
    background: var(--card);
    box-shadow: 0 10px 30px rgba(0,0,0,0.45);
    display: flex;
    flex-direction: column;
    align-items: center;
    justify-content: center;
  }
  .card::after {
    content: "";
    position: absolute;
    left: 0; right: 0; bottom: 0;
    height: 8px;
    background: var(--teal);
  }
  .card--front { height: 330px; }

  .brand {
    display: flex;
    flex-direction: column;
    align-items: center;
    gap: 18px;
    margin-bottom: 10px;
  }
  .brand__dot {
    width: 22px;
    height: 22px;
    border-radius: 50%;
    background: var(--teal);
  }
  .brand__name {
    font-family: "Noto Serif", Georgia, serif;
    font-weight: 700;
    color: var(--teal);
    text-align: center;
    letter-spacing: 0.06em;
    line-height: 1.35;
  }
  .brand__title { font-size: 38px; text-transform: uppercase; display: block; }
  .brand__tagline { font-size: 15px; text-transform: uppercase; letter-spacing: 0.32em; display: block; }

  .contact {
    display: flex;
    flex-direction: column;
    align-items: center;
    font-family: "Roboto", Arial, sans-serif;
    color: var(--white);
  }
  .contact__name {
    font-family: "Noto Serif", Georgia, serif;
    font-weight: 700;
    font-size: 36px;
    color: var(--teal);
    letter-spacing: 0.02em;
  }
  .contact__role { font-size: 20px; margin-top: 2px; }
  .contact__rule {
    width: 56px;
    height: 2px;
    background: var(--white);
    margin: 22px 0 20px;
  }
  .contact__line {
    display: flex;
    align-items: center;
    gap: 8px;
    font-size: 21px;
    line-height: 1.4;
  }
  .contact__line svg { flex: none; }
  .contact__abn { margin-top: 14px; font-size: 22px; }
  .contact__abn-label { color: var(--teal); font-weight: 500; }
</style>
</head>
<body>
  <main class="sheet">
    <section class="card card--front" aria-label="Card front">
      <div class="brand">
        <span class="brand__dot"></span>
        <p class="brand__name">
          <span class="brand__title">Silver Bloom</span>
          <span class="brand__tagline">Marisol's Cleaning Service</span>
        </p>
      </div>
    </section>

    <section class="card card--back" aria-label="Card back">
      <div class="contact">
        <h1 class="contact__name">Marisol Quenby</h1>
        <p class="contact__role">Director</p>
        <span class="contact__rule"></span>
        <p class="contact__line">
          <svg width="18" height="18" viewBox="0 0 24 24" aria-hidden="true">
            <path fill="#6dcfd0" d="M6.6 10.8a15.1 15.1 0 0 0 6.6 6.6l2.2-2.2a1 1 0 0 1 1-.25 11.4 11.4 0 0 0 3.6.57 1 1 0 0 1 1 1V20a1 1 0 0 1-1 1A17 17 0 0 1 3 4a1 1 0 0 1 1-1h3.5a1 1 0 0 1 1 1c0 1.25.2 2.46.57 3.6a1 1 0 0 1-.25 1z"/>
          </svg>
          0417906354
        </p>
        <p class="contact__line">
          <svg width="22" height="16" viewBox="0 0 22 16" aria-hidden="true">
            <rect x="1" y="1" width="20" height="14" fill="none" stroke="#6dcfd0" stroke-width="1.6"/>
            <path d="M1 1l10 8 10-8" fill="none" stroke="#6dcfd0" stroke-width="1.6"/>
          </svg>
          marisolssilvercleaning@tidymail.example
        </p>
        <p class="contact__line contact__abn">
          <span class="contact__abn-label">ABN:</span> 31647209853
        </p>
      </div>
    </section>
  </main>
</body>
</html>
```